Indy Film Production Company/Studio

We need a business card designed from an existing logo. We are a digital studio/production company that caters to creating genre entertainment, like Action, Horror, and martial arts. The card along with the logo will be used to Brand the company from letter heads to banners. The design will also be used for postcards and Brochures. It should be professional and masculine.
Updates

Thank you to all the designers who have participated. I'm narrowing down who it will be. Thank you again.

Target Market(s)

Investors, Networks, Producers, and actors

Industry/Entity Type

Film Production

Contact Information for Business Card

Teodoro Valbuena
Producer/Writer/Director
www.kestrelpicturehouse.example

Requirements
Must have
• Website address, Facebook icon and Twitter icon possibly in the back of the card.
Nice to have
• Logline of Company: Follow The Action.

```html
<!DOCTYPE html>
<html lang="en">
<head>
<meta charset="utf-8">
<title>Kestrel Picture House – Business Card</title>
<link rel="stylesheet" href="https://fonts.googleapis.com/css2?family=Montserrat:ital,wght@0,700;1,700&family=Roboto:wght@400&display=swap">
<style>
  :root {
    --backdrop: #a09d9d;
    --brand-red: #cc2f28;
    --card-white: #f3f2f0;
    --ink: #1e1c1c;
    --ink-soft: #2b2929;
    --rule: #dddad6;
    --on-red: #ffffff;
  }
  * { margin: 0; padding: 0; box-sizing: border-box; }
  html, body {
    width: 1200px; height: 1200px; overflow: hidden;
    background: var(--backdrop);
  }
  .canvas { position: relative; width: 1200px; height: 1200px; }

  .card { position: absolute; overflow: hidden; }

  /* Front */
  .card-front {
    left: 238px; top: 118px; width: 704px; height: 419px;
    background: var(--brand-red);
    display: flex; align-items: center; justify-content: center;
  }
  .wordmark {
    font-family: "Montserrat", sans-serif;
    font-weight: 700;
    text-transform: uppercase;
    text-align: center;
    line-height: 1.1;
    letter-spacing: 1px;
  }
  .card-front .wordmark { color: var(--on-red); font-size: 40px; }

  /* Back */
  .card-back {
    left: 231px; top: 644px; width: 711px; height: 418px;
    background: var(--card-white);
  }
  .card-back .wordmark {
    position: absolute; left: 0; top: 130px; width: 356px;
    color: var(--brand-red); font-size: 32px;
  }
  .divider {
    position: absolute; left: 356px; top: 56px;
    width: 1px; height: 300px; background: var(--rule);
  }
  .contact {
    position: absolute; left: 384px; top: 98px;
    font-family: "Roboto", sans-serif; color: var(--ink);
  }
  .contact-name {
    font-family: "Montserrat", sans-serif; font-weight: 700; font-style: italic;
    font-size: 26px; line-height: 1;
  }
  .contact-role {
    margin-top: 10px; font-size: 16px; color: var(--brand-red);
  }
  .contact-list { list-style: none; margin-top: 30px; font-size: 18px; }
  .contact-list li { display: flex; align-items: center; height: 28px; }
  .contact-list svg { width: 16px; height: 14px; margin-right: 18px; fill: var(--brand-red); }
  .contact-address { font-size: 18px; line-height: 28px; }

  .footer-band { position: absolute; left: 0; bottom: 0; width: 711px; height: 54px; }
  .footer-url {
    position: absolute; left: 384px; bottom: 18px;
    font-family: "Roboto", sans-serif; font-size: 16px; color: var(--on-red);
  }
  .social-links {
    position: absolute; right: 22px; bottom: 18px;
    display: flex; gap: 8px;
  }
  .social-dot {
    width: 18px; height: 18px; border-radius: 50%;
    background: var(--on-red);
  }
</style>
</head>
<body>
<main class="canvas">

  <section class="card card-front" aria-label="Card front">
    <div class="wordmark">Kestrel<br>Picture House</div>
  </section>

  <section class="card card-back" aria-label="Card back">
    <div class="wordmark">Kestrel<br>Picture House</div>
    <div class="divider"></div>

    <div class="contact">
      <div class="contact-name">Teodoro Valbuena</div>
      <div class="contact-role">Producer/Writer/Director</div>
      <ul class="contact-list">
        <li>
          <svg viewBox="0 0 16 14" aria-hidden="true"><path d="M1 5c0-2 3-4 7-4s7 2 7 4l-3 1-1-2H5L4 6 1 5zM3 7h10l1 6H2z"/></svg>
          +00 111 222 3333
        </li>
        <li>
          <svg viewBox="0 0 16 14" aria-hidden="true"><path d="M1 2h14v10H1zM2 3l6 5 6-5" stroke="#f3f2f0" stroke-width="1.2"/></svg>
          yourname@yourwebsite.com
        </li>
      </ul>
      <p class="contact-address">Your Long Commercial or<br>business address in 2 line</p>
    </div>

    <svg class="footer-band" viewBox="0 0 711 54" aria-hidden="true">
      <rect x="0" y="28" width="340" height="26" fill="var(--ink-soft)"/>
      <polygon points="342,0 711,0 711,54 314,54" fill="var(--brand-red)"/>
    </svg>
    <div class="footer-url">www.kestrelpicturehouse.example</div>
    <div class="social-links">
      <span class="social-dot" role="img" aria-label="Social profile link"></span>
      <span class="social-dot" role="img" aria-label="Social profile link"></span>
    </div>
  </section>

</main>
</body>
</html>
```